Business Card Design

New business card design

Target Market(s)

Residential & Commercial Property Managers

Industry/Entity Type

Plumbing Services

Contact Information for Business Card

Name - Rowan Keddle, title - Director, Phone Number - 0431 286 517, email - rowan@tbk-plumbing.com.au, Company ABN - 73 215 904 386,

Font styles to use
Sans Serif

Colors
0054AA
0677BA
7BADD7
CADEEF
E8F1F8

```html
<!DOCTYPE html>
<html lang="en">
<head>
<meta charset="utf-8">
<title>TBK Plumbing Services – Business Card</title>
<link rel="stylesheet" href="https://fonts.googleapis.com/css2?family=Montserrat:wght@300;400;500;700&display=swap">
<style>
  :root {
    --backdrop: #3a3b3e;
    --navy: #1d232b;
    --navy-soft: #232a33;
    --paper: #fbfbfb;
    --ink: #1e242c;
    --taupe: #8c7e72;
    --white: #ffffff;
  }
  * { margin: 0; padding: 0; box-sizing: border-box; }
  html, body {
    width: 1200px; height: 900px; overflow: hidden;
    background: var(--backdrop);
    font-family: "Montserrat", Arial, sans-serif;
  }
  .stage { position: relative; width: 1200px; height: 900px; }
  .card {
    position: absolute; left: 330px;
    width: 540px; height: 308px;
    border-radius: 18px; overflow: hidden;
    box-shadow: 0 10px 30px rgba(0,0,0,.35);
  }

  /* Back of card */
  .card--back {
    top: 100px;
    background: linear-gradient(160deg, var(--navy) 0%, var(--navy-soft) 100%);
    display: flex; flex-direction: column; align-items: center; justify-content: center;
  }
  .wordmark {
    font-weight: 500; font-size: 96px; line-height: 1;
    letter-spacing: 4px; text-transform: lowercase;
  }
  .card--back .wordmark { color: var(--white); }
  .tagline {
    font-weight: 300; font-size: 15px; color: var(--taupe);
    letter-spacing: 13px; margin-top: 14px; text-transform: lowercase;
    white-space: nowrap;
  }

  /* Front of card */
  .card--front { top: 480px; background: var(--paper); }
  .front__brand { position: absolute; left: 48px; top: 30px; }
  .card--front .wordmark { color: var(--ink); font-size: 100px; }
  .card--front .tagline { margin-top: 8px; letter-spacing: 15px; }

  .front__person {
    position: absolute; left: 70px; top: 194px; width: 178px;
    text-align: right; white-space: nowrap;
  }
  .person__name { font-weight: 700; font-size: 20px; color: var(--ink); }
  .person__title { font-weight: 400; font-size: 12px; color: var(--ink); margin-top: 2px; }

  .front__divider {
    position: absolute; left: 262px; top: 184px;
    width: 2px; height: 60px; background: var(--ink);
  }

  .front__contacts {
    position: absolute; left: 278px; top: 184px;
    list-style: none;
  }
  .contact {
    display: flex; align-items: center; gap: 8px;
    font-size: 12px; color: var(--ink); height: 20px;
    white-space: nowrap;
  }
  .contact svg { width: 12px; height: 12px; fill: var(--ink); flex: none; }

  .front__band {
    position: absolute; left: 0; right: 0; bottom: 14px; height: 36px;
    background: var(--navy);
    display: flex; align-items: center; justify-content: center;
    color: var(--white); font-size: 12px; letter-spacing: .3px;
  }
  .front__band strong { font-weight: 700; margin-right: 4px; }
</style>
</head>
<body>
<main class="stage">

  <section class="card card--back" aria-label="Business card back">
    <div class="wordmark">tbk</div>
    <div class="tagline">plumbing services</div>
  </section>

  <section class="card card--front" aria-label="Business card front">
    <div class="front__brand">
      <div class="wordmark">tbk</div>
      <div class="tagline">plumbing services</div>
    </div>

    <div class="front__person">
      <div class="person__name">Rowan Keddle</div>
      <div class="person__title">Director</div>
    </div>

    <div class="front__divider"></div>

    <ul class="front__contacts">
      <li class="contact">
        <svg viewBox="0 0 24 24" aria-hidden="true"><path d="M6.6 10.8a15.1 15.1 0 0 0 6.6 6.6l2.2-2.2c.3-.3.7-.4 1-.2 1.1.4 2.3.6 3.6.6.6 0 1 .4 1 1V20c0 .6-.4 1-1 1A17 17 0 0 1 3 4c0-.6.4-1 1-1h3.5c.6 0 1 .4 1 1 0 1.3.2 2.5.6 3.6.1.3 0 .7-.2 1z"/></svg>
        <span>0431 286 517</span>
      </li>
      <li class="contact">
        <svg viewBox="0 0 24 24" aria-hidden="true"><path d="M2 5h20v14H2z M2 5l10 8 10-8"/></svg>
        <span>rowan@tbk-plumbing.com.au</span>
      </li>
      <li class="contact">
        <svg viewBox="0 0 24 24" aria-hidden="true"><path d="M12 2a10 10 0 1 0 0 20 10 10 0 0 0 0-20zm0 2c.9 1.2 1.6 2.6 2 4h-4c.4-1.4 1.1-2.8 2-4zM4.3 14a8 8 0 0 1 0-4h3.4a16 16 0 0 0 0 4zm5.4 0a14 14 0 0 1 0-4h4.6a14 14 0 0 1 0 4zm6.6 0a16 16 0 0 0 0-4h3.4a8 8 0 0 1 0 4z"/></svg>
        <span>www.tbk-plumbing.com.au</span>
      </li>
    </ul>

    <div class="front__band"><strong>ABN</strong> - 73 215 904 386</div>
  </section>

</main>
</body>
</html>
```